Flyer Design Project

I need to create a flyer to advertise an Luxury Self Catering Apartment Complex in a Ski Resort in Europe. The development offers luxury accommodation to those who are on a budget.

Below is what needs to be included and a basic layout design idea i had that can be changed. The information is important. Hoping to get it on a flyer sized 21.6 x 14 cm

Title - 'Luxury Self Catering Ski Apartments For Rent'
Sub Title - 'Located 200m from Gondola, Restaurants and Bars'

Studio - Sleeps 1-2 - From only £200 per week
1 Bed - Sleeps 2-4 - From only £250 per week
2 Bed - Sleeps 4-6 - From only £350 per week

Image 1 Image 2 Image 3

- Fully Furnished Modern, Spacious & Comfortable Apartments
- Fully Staffed Development (Reception, Bar + Daily Cleaning)
- Family friendly & suitable for children of all ages

(Twitter Icon) @frostlodgevela
E-mail - frostlodgevela@mailbrook.co.uk
Telephone - +44 (0) 7700 913 284

Target Market(s)

Our target market is very wide. We are trying to attract students, couples and families who are skiing on a budget.

Industry/Entity Type

Accommodation

Requirements
Must have
• The text contained in 'task description' is important but i'd like to be led on design. Size of around 21.6 x 14cm is important and i'd like the 3 images below (hopefully someone can get of the date and time in orange bottom right of all pics)

http://img204.picvaultia.com/albums/qx512/tmrpics/Resort/318_00_640_kqra41c9.jpeg

http://img204.picvaultia.com/albums/qx512/tmrpics/Resort/b_02_kqrb6620.jpeg

http://img204.picvaultia.com/albums/qx512/tmrpics/Resort/318_08_640_kqrc93d7.jpeg

```html
<!DOCTYPE html>
<html lang="en">
<head>
<meta charset="utf-8">
<title>Luxury Self Catering Ski Apartments For Rent</title>
<link rel="stylesheet" href="https://fonts.googleapis.com/css2?family=Oswald:wght@300;500;600&family=Sansita:wght@700&family=Crimson+Text:wght@400;700&family=PT+Sans:wght@400;700&display=swap">
<style>
  :root {
    --page-bg: #e7e2da;
    --maroon: #5a1416;
    --maroon-deep: #3f0b0c;
    --gold: #d3a24a;
    --gold-light: #f0cf86;
    --gold-dark: #a8741f;
    --cream: #fbf1dc;
    --cream-deep: #f3dfb6;
    --ink: #3a1a10;
    --text-dark: #4a1c12;
    --white: #ffffff;
  }
  * { margin: 0; padding: 0; box-sizing: border-box; }
  html, body { width: 1200px; height: 900px; overflow: hidden; }
  body { background: var(--page-bg); position: relative; }

  .flyer {
    position: absolute; left: 305px; top: 28px;
    width: 542px; height: 838px;
    background: var(--white);
    overflow: hidden;
    box-shadow: 0 6px 18px rgba(0,0,0,0.25);
  }
  .flyer-shapes { position: absolute; inset: 0; }

  .title {
    position: absolute; left: 0; right: 0; top: 28px;
    text-align: center;
    font-family: "Oswald", sans-serif; font-weight: 500;
    font-size: 26px; color: var(--gold-light); letter-spacing: 0.2px;
  }
  .subtitle {
    position: absolute; left: 0; right: 0; top: 64px;
    text-align: center;
    font-family: "Oswald", sans-serif; font-weight: 300;
    font-size: 21px; color: var(--white);
  }

  .thumb {
    position: absolute; left: 15px; width: 147px; height: 87px;
    border: 4px solid var(--gold);
    box-shadow: 0 2px 5px rgba(0,0,0,0.35);
  }
  .thumb-bedroom { top: 449px; background: linear-gradient(120deg, #8a5a3a, #d8c2a0 45%, #f2e8d8 70%, #6b3a22); }
  .thumb-lounge { top: 557px; background: linear-gradient(120deg, #5a3a28, #e8e4dc 40%, #f6f4ef 65%, #8a6a50); }
  .thumb-kitchen { top: 665px; background: linear-gradient(120deg, #2a1a14, #6b4a36 40%, #d8d2c8 70%, #3a2418); }

  .details { position: absolute; left: 178px; width: 350px; top: 437px; color: var(--text-dark); }
  .location {
    text-align: center; font-family: "Sansita", sans-serif; font-weight: 700;
    font-size: 26px; color: var(--maroon); line-height: 32px;
  }
  .award-source, .award-title {
    text-align: center; font-family: "PT Sans", sans-serif; font-weight: 700;
    color: var(--maroon);
  }
  .award-source { font-size: 14px; line-height: 17px; }
  .award-title { font-size: 15.5px; line-height: 18px; }

  .press { margin-top: 8px; padding-left: 5px; font-family: "Crimson Text", serif; font-size: 15.5px; line-height: 17px; color: var(--ink); }
  .press-source { font-weight: 700; font-size: 16px; color: var(--maroon-deep); }

  .features { list-style: none; margin-top: 13px; padding-left: 5px; font-family: "Crimson Text", serif; font-size: 15.5px; line-height: 17px; color: var(--ink); }
  .features li { position: relative; padding-left: 19px; margin-bottom: 4px; }
  .features li.gap { margin-bottom: 10px; }
  .features li::before {
    content: ""; position: absolute; left: 0; top: 3px;
    width: 0; height: 0;
    border-top: 5px solid transparent; border-bottom: 5px solid transparent;
    border-left: 12px solid var(--maroon-deep);
  }
  .price { font-family: "PT Sans", sans-serif; font-weight: 700; color: var(--maroon); }

  .contact { position: absolute; left: 30px; top: 775px; font-family: "PT Sans", sans-serif; color: var(--white); font-size: 14.5px; line-height: 20px; }
  .contact-heading { padding-left: 22px; font-size: 15px; }
  .contact-row { display: flex; align-items: center; gap: 8px; }
  .contact-icon { width: 12px; height: 12px; flex: none; }
  .social-mark { display: inline-block; width: 11px; height: 11px; background: var(--gold); margin-left: 14px; }
</style>
</head>
<body>
  <main class="flyer">
    <svg class="flyer-shapes" width="542" height="838" viewBox="0 0 542 838" aria-hidden="false">
      <defs>
        <linearGradient id="header-grad" x1="0" y1="0" x2="1" y2="0">
          <stop offset="0" stop-color="var(--maroon-deep)"/>
          <stop offset="0.5" stop-color="var(--maroon)"/>
          <stop offset="1" stop-color="var(--maroon-deep)"/>
        </linearGradient>
        <linearGradient id="gold-grad" x1="0" y1="0" x2="1" y2="0">
          <stop offset="0" stop-color="var(--gold-dark)"/>
          <stop offset="0.5" stop-color="var(--gold-light)"/>
          <stop offset="1" stop-color="var(--gold-dark)"/>
        </linearGradient>
        <linearGradient id="cream-grad" x1="0" y1="0" x2="0" y2="1">
          <stop offset="0" stop-color="var(--cream-deep)"/>
          <stop offset="1" stop-color="var(--cream)"/>
        </linearGradient>
        <linearGradient id="photo-grad" x1="0" y1="0" x2="1" y2="1">
          <stop offset="0" stop-color="#f4f4f2"/>
          <stop offset="0.35" stop-color="#b79a78"/>
          <stop offset="0.6" stop-color="#e9e6e0"/>
          <stop offset="1" stop-color="#5a4a3c"/>
        </linearGradient>
      </defs>

      <rect x="0" y="100" width="542" height="350" fill="url(#photo-grad)" role="img" aria-label="Photograph of the stone and white-rendered apartment building with balconies"/>

      <path d="M0 0 H542 V90 C470 120 360 135 250 133 C150 131 60 150 0 180 Z" fill="url(#header-grad)"/>
      <path d="M542 82 C470 118 360 130 250 128 C150 126 70 138 0 168 V180 C60 150 150 131 250 133 C360 135 470 120 542 98 Z" fill="url(#gold-grad)"/>

      <path d="M0 438 C90 400 220 392 330 398 C430 404 500 392 542 372 V838 H0 Z" fill="url(#cream-grad)"/>
      <path d="M0 428 C90 392 220 384 330 390 C430 396 500 384 542 364 V376 C500 396 430 408 330 402 C220 396 90 404 0 442 Z" fill="url(#gold-grad)"/>

      <path d="M0 778 C120 758 280 762 400 770 C470 774 515 768 542 760 V838 H0 Z" fill="url(#header-grad)"/>
      <path d="M0 772 C120 752 280 756 400 764 C470 768 515 762 542 754 V762 C515 770 470 776 400 772 C280 764 120 760 0 780 Z" fill="url(#gold-grad)"/>
    </svg>

    <h1 class="title">Luxury Self Catering Ski Apartments For Rent</h1>
    <p class="subtitle">Located 200m from Gondola, Restaurants and Bars</p>

    <div class="thumb thumb-bedroom" role="img" aria-label="Photograph of an apartment bedroom with double bed"></div>
    <div class="thumb thumb-lounge" role="img" aria-label="Photograph of an apartment living room with sofa"></div>
    <div class="thumb thumb-kitchen" role="img" aria-label="Photograph of an apartment kitchen and dining area"></div>

    <section class="details">
      <h2 class="location">Bansko - Bulgaria</h2>
      <p class="award-source">TravelVerdict</p>
      <p class="award-title">Best Value Ski Resort in Europe 2011 + 2012</p>

      <div class="press">
        <p class="press-source">The Daily Meridian</p>
        <p>Bansko has been transformed into a winter<br>destination that can truly compete with<br>the Alps - at a fraction of the cost.</p>
      </div>

      <ul class="features">
        <li>Fully Furnished Modern,<br>Spacious &amp; Comfortable Apartments</li>
        <li>Fully Staffed Development<br>(Reception, Bar + Daily Cleaning)</li>
        <li class="gap">Family friendly &amp; suitable for children of all ages</li>
        <li>Studio - Sleeps 1-2 - From only <span class="price">£200</span> per week</li>
        <li>1 Bed - Sleeps 2-4 - From only <span class="price">£250</span> per week</li>
        <li>2 Bed - Sleeps 4-6 - From only <span class="price">£350</span> per week</li>
      </ul>
    </section>

    <footer class="contact">
      <p class="contact-heading">CONTACT US :</p>
      <p class="contact-row">
        <svg class="contact-icon" viewBox="0 0 12 12"><path d="M2.5 0.8 L4.4 3.2 L3.3 4.4 C4 6 5.6 7.7 7.4 8.6 L8.6 7.5 L11 9.4 L9.8 11.2 C5.2 10.6 1.2 6.6 0.6 2 Z" fill="var(--gold)"/></svg>
        +44 (0) 7700 913 284
      </p>
      <p class="contact-row">
        <svg class="contact-icon" viewBox="0 0 12 12"><rect x="0.5" y="2.5" width="11" height="7.5" fill="var(--gold)"/><path d="M0.5 2.5 L6 7 L11.5 2.5" fill="none" stroke="var(--maroon-deep)" stroke-width="1"/></svg>
        frostlodgevela@mailbrook.co.uk
        <span class="social-mark"></span>@frostlodgevela
      </p>
    </footer>
  </main>
</body>
</html>
```